Larkspur Talent IT Recruiting firm needs a business card design for Recruiters, Sourcers, and Account

We need business cards that allow us to change all contact info, names, titles (Recruiter, Sourcer, Account Manager, Director, CEO, etc) per person since we have three offices, in three cities, Phoenix, Austin, and Las Vegas. We do recruiting and contractors for IT positions (Developers, Architects, Software Engineers, Security Engineers, Help Desk, DBAs, PMs, Scrum Masters, etc.) Our client companies are very diverse from Meridian 100 to silicone Valley type start-ups.

So, while we what hip, techie, and quirky, it still needs to be professional. Primary color we use is blue, with silver as a secondary color.

Target Market(s)

IT, Technology

Industry/Entity Type

Business

Contact Information for Business Card

Company name: Larkspur Talent, Inc.
Website: www.larkspurtalent.example
Logos for Careerloop, Blipster, and Myriada

Name, Title, Office Number, Cell Number, email

Font styles to use
Serif
Sans Serif

Colors
0455a3
d5d5d5

Requirements
Nice to have
• The grey I selected below is not necessary - but, would like silver included. I included a card design (File 3: LTI early trial example.jpg) that I had started on. It's very rough, and not quite what we're looking for, but what we did like is the logo, big, maybe a bit faded, off center, goes out of frame, etc. Still looking for other ideas - you are the pros! But, just an idea of a design element we liked.

```html
<!DOCTYPE html>
<html lang="en">
<head>
<meta charset="utf-8">
<title>Larkspur Talent — Business Card</title>
<link rel="stylesheet" href="https://fonts.googleapis.com/css2?family=Marcellus&family=Arimo:wght@400;700&display=swap">
<style>
  :root {
    --brand-blue: #0455a3;
    --brand-blue-deep: #034a8e;
    --brand-blue-light: #1a6bbd;
    --silver: #d5d5d5;
    --ink-grey: #6d6d6d;
    --paper: #ffffff;
    --stage: #eceef1;
    --serif: "Marcellus", serif;
    --sans: "Arimo", sans-serif;
  }
  html, body {
    margin: 0;
    padding: 0;
    width: 1200px;
    height: 902px;
    overflow: hidden;
    background: var(--stage);
  }
  .stage {
    width: 1200px;
    height: 902px;
    display: flex;
    align-items: center;
    justify-content: center;
    gap: 40px;
  }
  .card {
    position: relative;
    width: 540px;
    height: 309px;
    border-radius: 16px;
    overflow: hidden;
    box-shadow: 0 10px 28px rgba(0, 0, 0, 0.18);
  }

  /* ---------- Brand name ---------- */
  .brand {
    display: inline-flex;
    align-items: center;
    gap: 10px;
  }
  .brand-dot {
    flex: 0 0 auto;
    border-radius: 50%;
  }
  .brand-name {
    font-family: var(--serif);
    font-weight: 400;
    line-height: 1;
    margin: 0;
    white-space: nowrap;
  }
  .specialty {
    font-family: var(--sans);
    font-weight: 400;
    margin-top: 12px;
  }

  /* ---------- Front ---------- */
  .card-front {
    background: linear-gradient(135deg, var(--brand-blue-light) 0%, var(--brand-blue) 55%, var(--brand-blue-deep) 100%);
    color: var(--paper);
  }
  .front-emblem {
    position: absolute;
    right: -70px;
    top: -90px;
    width: 300px;
    height: 300px;
    border-radius: 50%;
    background: rgba(0, 40, 100, 0.28);
  }
  .front-rule {
    position: absolute;
    right: 58px;
    top: 0;
    bottom: 0;
    width: 1px;
    background: rgba(120, 190, 255, 0.55);
  }
  .front-logo {
    position: absolute;
    left: 0;
    right: 0;
    top: 108px;
    text-align: center;
  }
  .front-logo .brand-dot {
    width: 18px;
    height: 18px;
    background: var(--paper);
  }
  .front-logo .brand-name {
    font-size: 36px;
    color: var(--paper);
  }
  .front-logo .specialty {
    font-size: 12px;
    letter-spacing: 1px;
    color: rgba(255, 255, 255, 0.85);
  }
  .front-website {
    position: absolute;
    left: 0;
    right: 0;
    bottom: 46px;
    text-align: center;
    font-family: var(--sans);
    font-size: 19px;
    letter-spacing: 0.3px;
  }

  /* ---------- Back ---------- */
  .card-back { background: var(--paper); }
  .back-emblem {
    position: absolute;
    left: 70px;
    bottom: -120px;
    width: 230px;
    height: 230px;
    border-radius: 50%;
    background: var(--silver);
    opacity: 0.55;
  }
  .back-logo {
    position: absolute;
    left: 0;
    width: 290px;
    top: 100px;
    text-align: center;
  }
  .back-logo .brand-dot {
    width: 13px;
    height: 13px;
    background: var(--brand-blue);
  }
  .back-logo .brand-name {
    font-size: 25px;
    color: var(--brand-blue);
  }
  .back-logo .specialty {
    font-size: 10px;
    letter-spacing: 0.8px;
    color: var(--ink-grey);
  }
  .social {
    position: absolute;
    left: 26px;
    bottom: 22px;
    font-family: var(--sans);
    color: var(--brand-blue);
  }
  .social-networks { font-size: 10px; color: var(--ink-grey); margin-bottom: 3px; }
  .social-handle { font-size: 14px; font-weight: 700; }

  .contact-panel {
    position: absolute;
    left: 290px;
    top: 0;
    right: 0;
    bottom: 0;
    background: linear-gradient(160deg, var(--brand-blue-light) 0%, var(--brand-blue) 60%, var(--brand-blue-deep) 100%);
    color: var(--paper);
    font-family: var(--sans);
    padding: 34px 20px 0 30px;
  }
  .contact-panel::before {
    content: "";
    position: absolute;
    left: 0;
    top: 46px;
    border-top: 9px solid transparent;
    border-bottom: 9px solid transparent;
    border-left: 10px solid var(--paper);
  }
  .person-name {
    font-size: 19px;
    letter-spacing: 0.5px;
    margin: 0;
  }
  .person-title {
    font-size: 13px;
    margin: 4px 0 26px;
    opacity: 0.9;
  }
  .contact-list {
    list-style: none;
    margin: 0;
    padding: 0;
    font-size: 11.5px;
    line-height: 1.35;
  }
  .contact-list li {
    display: flex;
    align-items: flex-start;
    gap: 8px;
    margin-bottom: 7px;
  }
  .contact-list svg {
    flex: 0 0 12px;
    width: 12px;
    height: 12px;
    margin-top: 1px;
    fill: var(--paper);
  }
</style>
</head>
<body>
<main class="stage">

  <section class="card card-front" aria-label="Card front">
    <div class="front-emblem" aria-hidden="true"></div>
    <div class="front-rule" aria-hidden="true"></div>
    <div class="front-logo">
      <div class="brand">
        <span class="brand-dot" aria-hidden="true"></span>
        <p class="brand-name">Larkspur Talent</p>
      </div>
      <div class="specialty">IT Recruiting &amp; Contracting</div>
    </div>
    <div class="front-website">www.larkspurtalent.example</div>
  </section>

  <section class="card card-back" aria-label="Card back">
    <div class="back-emblem" aria-hidden="true"></div>
    <div class="back-logo">
      <div class="brand">
        <span class="brand-dot" aria-hidden="true"></span>
        <p class="brand-name">Larkspur Talent</p>
      </div>
      <div class="specialty">IT Recruiting &amp; Contracting</div>
    </div>
    <div class="social">
      <div class="social-networks">Careerloop · Blipster · Myriada</div>
      <div class="social-handle">@larkspurtalent</div>
    </div>

    <div class="contact-panel">
      <p class="person-name">YOUR NAME</p>
      <p class="person-title">Title</p>
      <ul class="contact-list">
        <li>
          <svg viewBox="0 0 12 12" aria-hidden="true"><path d="M6 0a4 4 0 0 1 4 4c0 3-4 8-4 8S2 7 2 4a4 4 0 0 1 4-4zm0 2.5a1.5 1.5 0 1 0 0 3 1.5 1.5 0 0 0 0-3z"/></svg>
          <span>2210 E Copperline Rd, Suite 140<br>Phoenix, AZ 85034, USA</span>
        </li>
        <li>
          <svg viewBox="0 0 12 12" aria-hidden="true"><path d="M2.5 0.5l2 2.5-1 1.5a7 7 0 0 0 4 4l1.5-1 2.5 2-1.2 1.8C5.5 11.5 0.5 6.5 0.7 1.7z"/></svg>
          <span>(602) 555-0148</span>
        </li>
        <li>
          <svg viewBox="0 0 12 12" aria-hidden="true"><path d="M3 0h6a1 1 0 0 1 1 1v10a1 1 0 0 1-1 1H3a1 1 0 0 1-1-1V1a1 1 0 0 1 1-1zm0.5 1.5v7.5h5V1.5z"/></svg>
          <span>(602) 555-0193</span>
        </li>
        <li>
          <svg viewBox="0 0 12 12" aria-hidden="true"><path d="M0 2h12v8H0zm1 1v0.4l5 3.3 5-3.3V3z"/></svg>
          <span>jordan@larkspurtalent.example</span>
        </li>
        <li>
          <svg viewBox="0 0 12 12" aria-hidden="true"><path d="M6 0a6 6 0 1 1 0 12A6 6 0 0 1 6 0zm0 1.2c-1 0-1.8 2.1-1.8 4.8s.8 4.8 1.8 4.8 1.8-2.1 1.8-4.8S7 1.2 6 1.2zM1.3 5.4h9.4v1.2H1.3z"/></svg>
          <span>www.larkspurtalent.example</span>
        </li>
      </ul>
    </div>
  </section>

</main>
</body>
</html>
```